BUSINESS CARD - HALLORAN FIELD SERVICES

I would like to create a business card for my fertilizer spreading business. I would like to incorporate my existing logo and also a description of the services offered. The business card will be given to farmers so must be kept simple but effective. It will also be left in stores so much also be eye catching in order to stand out from other cards.

Target Market(s)

FARMERS

Requirements
Must have
• FRONT OF CARD = EXISTING LOGO + "CUSTOMISED SPREADING" below the logo

REAR Of CARD = SERVICES OFFERED AND CONTACT DETAILS

- Bulk fertilizer including Lime, Gypsum, Manure & Compost
- Granular fertilizer including Single Super, Urea, Gran-am, & Custom Blends
- Modern equipment - Autosteer & Variable Rate Capable
- Friendly & Reliable Service
- Contact Gus: 0417 552 308
Nice to have
• utilize same color scheme as existing logo

```html
<!DOCTYPE html>
<html lang="en">
<head>
<meta charset="utf-8">
<title>Halloran Field Services – Business Card</title>
<link rel="stylesheet" href="https://fonts.googleapis.com/css2?family=Open+Sans:wght@400;600;700&family=Exo+2:wght@700&display=swap">
<style>
  :root {
    --bg: #2a2a2b;
    --card: #1d1d1f;
    --ink-grey: #6f6f72;
    --ink-mid: #58585b;
    --accent: #f7941d;
    --rule: #4a4a4d;
    --pattern: #252527;
  }
  * { box-sizing: border-box; margin: 0; padding: 0; }
  html, body {
    width: 1200px; height: 1108px; overflow: hidden;
    background: var(--bg);
  }
  .stage {
    position: relative; width: 1200px; height: 1108px;
    display: flex; justify-content: center; align-items: center; gap: 60px;
  }
  .card {
    position: relative; width: 440px; height: 680px;
    background: var(--card); border-radius: 26px;
    box-shadow: 0 18px 40px rgba(0,0,0,.45);
    overflow: hidden;
    font-family: "Open Sans", sans-serif;
  }

  /* Rear: services + contact */
  .card--rear { display: flex; flex-direction: column; align-items: center; padding: 90px 34px 0; }
  .brand { display: flex; flex-direction: column; align-items: center; gap: 22px; }
  .brand__mark { width: 120px; height: 120px; border-radius: 50%; background: var(--ink-mid); }
  .brand__name {
    font-weight: 700; font-size: 27px; letter-spacing: 1px;
    color: var(--ink-grey); text-align: center; line-height: 1.2;
  }
  .services {
    list-style: none; margin-top: 44px; text-align: center;
    color: var(--ink-grey); font-size: 15.5px; line-height: 1.55; text-transform: uppercase;
  }
  .services li + li { margin-top: 4px; }
  .contact { margin-top: 46px; text-align: center; width: 100%; }
  .contact__label {
    display: flex; align-items: center; gap: 12px;
    color: var(--ink-grey); font-size: 20px; text-transform: uppercase;
  }
  .contact__label::before, .contact__label::after {
    content: ""; flex: 1; height: 1px; background: var(--rule);
  }
  .contact__line { margin-top: 6px; font-size: 24px; color: var(--ink-grey); }
  .contact__phone { color: var(--accent); }

  /* Front: pattern + mark + tagline */
  .pattern { position: absolute; inset: 0 0 170px 0; background: linear-gradient(160deg, var(--pattern), var(--card)); }
  .front-brand {
    position: absolute; left: 0; right: 0; top: 450px;
    display: flex; align-items: center; justify-content: center; gap: 14px;
  }
  .front-brand__mark { width: 54px; height: 54px; border-radius: 50%; background: var(--ink-mid); }
  .front-brand__name { font-weight: 700; font-size: 20px; color: var(--ink-grey); letter-spacing: 1px; }
  .tagline {
    position: absolute; left: 0; right: 0; bottom: 120px; text-align: center;
    font-family: "Exo 2", sans-serif; font-weight: 700; font-size: 31px;
    letter-spacing: 2px; color: var(--accent); text-transform: uppercase;
  }
</style>
</head>
<body>
<main class="stage">
  <section class="card card--rear" aria-label="Card rear">
    <div class="brand">
      <div class="brand__mark"></div>
      <div class="brand__name">HALLORAN FIELD<br>SERVICES</div>
    </div>
    <ul class="services">
      <li>Bulk fertilizer including lime<br>gypsum, manure &amp; compost</li>
      <li>Granular fertilizer including single<br>super, urea, gran-am, &amp; custom blends</li>
      <li>Modern equipment<br>autosteer &amp; variable rate capable</li>
      <li>Friendly &amp; reliable service</li>
    </ul>
    <div class="contact">
      <div class="contact__label">Contact</div>
      <div class="contact__line">GUS: <span class="contact__phone">0417 552 308</span></div>
    </div>
  </section>

  <section class="card card--front" aria-label="Card front">
    <div class="pattern" role="img" aria-label="Faint repeating pattern of the brand mark"></div>
    <div class="front-brand">
      <div class="front-brand__mark"></div>
      <div class="front-brand__name">HALLORAN FIELD SERVICES</div>
    </div>
    <div class="tagline">Customised Spreading</div>
  </section>
</main>
</body>
</html>
```